Bluefern Business Services needs a new interactive and interesting website

We need an interesting, professional, modern and functional company website for Bluefern Business Services - a young IT Services company based out of Chennai, India.

Bluefern Business Services is a fully owned subsidiary of Marlow Goods, one of the world's leading direct to consumer wine merchant.

We already have a registered company logo which must feature in the website.

We conceive, design, develop, test, implement and support IT solutions across the entire Marlow Goods IT landscape. For ex : We currently run about 25 e-commerce websites for Marlow Goods on ATG and Dot Net.

We would like to see our corporate colors used in the website. (Burgundy wine and wine green - source: www.bluefernbs-site.com)

We are looking at this website to communicate a fun, friendly and professionally managed company - reaching out to career seekers, prospective customers and general public.

For reference - The company name 'Bluefern' is an inspiration from the Marlow Goods lineage.

The second image with the world map is stickered on our main entrance to the office, I am not sure where this can be used -just putting it out there..

Please note that there are only a few more days to submit designs for this contest  !

I would appreciate if you can help posting your designs in time for our review and consideration.

Thanks.

Reason: Thanks for your inputs. We have a number of designers and a lot to digest and work with in the past few days. There has been a rush of new designs in the last few days Hence we will require more time to process these and make our decision. Hence i am requesting the contest to be open for more days. Regards, Tarun

Target Market(s)

Prospective job seekers who want to know more about the company and also wish to apply for a job vacancy
People wanting to know more about the company in general and our progress
People who want to see what we offer and how we can help them too - prospective customers
Companies that are interested in our IT Captive journey and are looking for a business opportunity

Industry/Entity Type

E-Commerce

Requirements
Must have
• Log In/ Register facility acting as a Single Sign on for Intranet (Employees)

Facility to post job vacancies (with an expiry date) and enable people to apply for a role and upload their CV/Resume.

Facility to Review Job applications

Facility for website visitors to contact Bluefern business Services via an online 'Contact Us' form with a split of job seekers and business opportunities

Gallery facility to upload pictures regarding company events
Nice to have
• Less Cluttered and contemporary design
Some Wine/Vineyard inspirations will be good but not too much, the company is an IT services company

```html
<!DOCTYPE html>
<html lang="en">
<head>
<meta charset="utf-8">
<title>Bluefern Business Services</title>
<link href="https://fonts.googleapis.com/css2?family=Source+Sans+3:wght@400;600;700&display=swap" rel="stylesheet">
<style>
:root{
  --wine:#8c0d46;
  --wine-dark:#6e0a37;
  --ink:#333;
  --muted:#777;
  --rule:#bdbdbd;
  --band:#eeeeee;
  --footer:#3a3a3a;
  --footer-bottom:#2f2f2f;
  --footer-text:#d8d8d8;
}
*{margin:0;padding:0;box-sizing:border-box}
html,body{width:1009px;height:1200px;overflow:hidden;background:#fff}
body{font-family:"Source Sans 3",Arial,sans-serif;color:var(--ink)}
.page{position:relative;width:1009px;height:1200px;overflow:hidden}
.abs{position:absolute}
.accent{color:var(--wine)}

/* header */
.site-header{left:0;top:0;width:1009px;height:100px;background:var(--wine)}
.brand{left:168px;top:20px;color:#fff;display:flex;align-items:flex-start;gap:8px}
.brand-dot{width:34px;height:34px;border-radius:50%;border:3px solid #fff;margin-top:8px}
.brand-name{font-size:44px;font-weight:700;line-height:40px;letter-spacing:-1px}
.brand-sub{font-size:26px;line-height:30px;font-weight:400;margin-left:40px}
.header-contact{top:43px;color:#fff;font-size:10px;display:flex;align-items:center;gap:6px}

/* nav */
.main-nav{left:0;top:100px;width:1009px;height:30px;background:linear-gradient(#f4f4f4,#dcdcdc);border-bottom:1px solid #c8c8c8}
.nav-item{top:0;height:30px;line-height:30px;font-size:11px;color:#333}
.nav-item.is-active{background:var(--wine);color:#fff;text-align:center}
.nav-search{left:814px;top:0;width:25px;height:30px;background:#f6f6f6;border-left:1px solid #c8c8c8;border-right:1px solid #c8c8c8;display:flex;align-items:center;justify-content:center}

/* hero */
.hero{left:0;top:130px;width:1009px;height:250px;background:linear-gradient(100deg,#3b3f4a 0%,#cfc8c0 25%,#e9e4de 45%,#b9a795 60%,#2e3340 80%,#d9d3cc 100%)}
.hero-card{left:167px;top:174px;width:322px;height:156px;background:rgba(255,255,255,.82);border:1px solid #d0d0d0;padding:9px 7px}
.hero-card h1{font-size:24px;font-weight:400;color:var(--wine);letter-spacing:-.5px;line-height:26px}
.hero-card h1 b{font-weight:700}
.hero-card p{font-size:8.5px;line-height:16px;color:#222;margin:8px 0 0 4px;width:270px}
.hero-card .more{font-size:11px;margin:10px 0 0 5px;color:#111}
.hero-arrow{top:223px;width:34px;height:47px;background:rgba(235,235,235,.92);display:flex;align-items:center;justify-content:center}
.hero-dots{left:201px;top:348px;display:flex;gap:4px}
.hero-dots span{width:7px;height:7px;border-radius:50%;background:#fff}
.hero-dots span:first-child{background:var(--wine)}

/* intro */
.section-title{left:0;width:1009px;text-align:center;font-weight:400;color:#222}
.intro-title{top:402px;font-size:26px}
.intro-text{left:174px;top:445px;width:660px;text-align:center;font-size:8.5px;line-height:12px;color:#555}
.btn{left:461px;top:481px;width:79px;height:26px;background:var(--wine);color:#fff;font-size:8px;font-weight:600;display:flex;align-items:center;justify-content:center}

/* services */
.services-title{top:540px;font-size:21px}
.service{top:594px;width:160px}
.service-head{display:flex;gap:4px;align-items:flex-start}
.service-head h3{font-size:12.5px;font-weight:400;color:var(--wine);line-height:12px;text-align:center}
.service p{font-size:7.5px;line-height:10px;color:#666;margin:8px 0 0 4px;width:150px}
.divider{left:170px;top:694px;width:671px;height:1px;background:var(--rule)}

/* events */
.events-title{top:708px;font-size:21px}
.slider-arrows{display:flex;gap:12px}
.events-band{left:0;top:744px;width:1009px;height:92px;background:var(--band)}
.event-media{top:752px;width:174px;height:74px;border:1px solid #ccc}
.event-media.vineyard{background:linear-gradient(160deg,#d9a640,#b88a3a 50%,#e8d9a8)}
.event-media.meeting{background:linear-gradient(100deg,#e6e3df,#5d6170 45%,#c9c4be 75%,#3d4150)}
.play{left:75px;top:28px;width:24px;height:17px;background:#111;border:1px solid #fff;display:flex;align-items:center;justify-content:center}
.event-text{top:756px;width:146px}
.event-text h4{font-size:12px;color:var(--wine);font-weight:700}
.event-text p{font-size:7.5px;line-height:10px;color:#888;margin-top:3px}

/* clients */
.clients-title{top:870px;font-size:21px;color:var(--wine)}
.client{top:905px;width:90px;height:60px;background:#fff;box-shadow:0 0 3px rgba(0,0,0,.12);display:flex;align-items:center;justify-content:center;text-align:center;font-size:11px;font-weight:700;color:var(--wine);line-height:12px}

/* footer */
.site-footer{left:0;top:990px;width:1009px;height:175px;background:var(--footer)}
.footer-bottom{left:0;top:1165px;width:1009px;height:35px;background:var(--footer-bottom)}
.footer-title{font-size:13px;color:#fff;font-weight:400}
.footer-text{font-size:7.5px;line-height:11px;color:var(--footer-text)}
.opp{left:197px;display:flex;gap:5px}
.opp-thumb{width:40px;height:30px}
.copyright{left:181px;top:1180px;font-size:7.5px;color:#ddd}
.social{top:1171px;width:22px;height:22px;background:#5a5a5a;color:#ccc;font-size:6px;display:flex;align-items:center;justify-content:center}
</style>
</head>
<body>
<div class="page">

  <header class="site-header abs">
    <div class="brand abs">
      <div class="brand-dot"></div>
      <div>
        <div class="brand-name">bluefern</div>
        <div class="brand-sub">Business Services</div>
      </div>
    </div>
    <div class="header-contact abs" style="left:580px">
      <svg width="12" height="10" viewBox="0 0 12 10"><path d="M1 4c0-3 10-3 10 0l-2 1-1-2H4L3 5z" fill="#fff"/><rect x="3" y="5" width="6" height="4" fill="#fff"/></svg>
      <span>+91 (44) 55501234</span>
    </div>
    <div class="header-contact abs" style="left:694px">
      <svg width="11" height="10" viewBox="0 0 11 10"><rect x="1" y="1" width="9" height="8" fill="none" stroke="#fff"/><path d="M1 1l4.5 4L10 1" fill="none" stroke="#fff"/></svg>
      <span>contactus@bluefernbs-site.com</span>
    </div>
  </header>

  <nav class="main-nav abs">
    <div class="nav-item is-active abs" style="left:168px;width:65px">Home</div>
    <div class="nav-item abs" style="left:259px">About us</div>
    <div class="nav-item abs" style="left:344px">Clients</div>
    <div class="nav-item abs" style="left:424px">Services</div>
    <div class="nav-item abs" style="left:514px">Careers</div>
    <div class="nav-item abs" style="left:594px">Contact</div>
    <div class="nav-item abs" style="left:665px">Current Opportunities</div>
    <div class="nav-search abs">
      <svg width="12" height="12" viewBox="0 0 12 12"><circle cx="5" cy="5" r="3.6" fill="none" stroke="#222" stroke-width="1.6"/><path d="M7.6 7.6L11 11" stroke="#222" stroke-width="1.8"/></svg>
    </div>
  </nav>

  <div class="hero abs" role="img" aria-label="Photo of a business team in conversation around a meeting table"></div>
  <div class="hero-card abs">
    <h1>WELCOME TO <b>BLUEFERNBS</b></h1>
    <p>Lorem ipsum dolor sit amet, consectetur adipiscing elit. Nunc sodales, nisi sodales pharetra hendrerit, tellus mi pharetra risus, sed porttitor sapien dui sit amet lacus. Duis sit amet elit nec turpis.Lorem ipsum dolor sit amet, consectetur adipiscing elit. Nunc sodales, nisi</p>
    <div class="more">LEARN MORE</div>
  </div>
  <div class="hero-arrow abs" style="left:0">
    <svg width="12" height="14" viewBox="0 0 12 14"><path d="M9 1L3 7l6 6" fill="none" stroke="#555" stroke-width="3"/></svg>
  </div>
  <div class="hero-arrow abs" style="left:975px">
    <svg width="12" height="14" viewBox="0 0 12 14"><path d="M3 1l6 6-6 6" fill="none" stroke="#555" stroke-width="3"/></svg>
  </div>
  <div class="hero-dots abs"><span></span><span></span></div>

  <h2 class="section-title intro-title abs">Welcome to <span class="accent">Bluefern Business Services</span></h2>
  <p class="intro-text abs">Lorem ipsum dolor sit amet, consectetur adipiscing elit. Nunc sodales, nisi sodales pharetra hendrerit, tellus mi pharetra risus, sed porttitor sapien dui sit amet lacus. Duis sit amet elit nec turpis.Lorem ipsum dolor sit amet, consectetur adipiscing elit. Nunc sodales, nisi sodales pharetra hendrerit</p>
  <div class="btn abs">Read more</div>

  <h2 class="section-title services-title abs">Our <span class="accent">Services</span></h2>

  <div class="service abs" style="left:179px">
    <div class="service-head">
      <svg width="24" height="22" viewBox="0 0 24 22"><rect x="4" y="3" width="12" height="11" fill="#222" transform="rotate(-12 10 8)"/><path d="M1 4l4 1 3 13h12" fill="none" stroke="#222" stroke-width="2"/><circle cx="9" cy="20" r="1.6" fill="#222"/><circle cx="18" cy="20" r="1.6" fill="#222"/></svg>
      <h3>Packaged Applications</h3>
    </div>
    <p>Lorem ipsum dolor sit amet, Lonsectetur adipiscing elit. Sed pulvinar tempor pellentesque</p>
  </div>

  <div class="service abs" style="left:347px">
    <div class="service-head">
      <svg width="24" height="22" viewBox="0 0 24 22"><circle cx="12" cy="11" r="7" fill="none" stroke="#222" stroke-width="4" stroke-dasharray="3 2.5"/><circle cx="12" cy="11" r="5" fill="#222"/><circle cx="12" cy="11" r="2" fill="#fff"/></svg>
      <h3>Enterprise Application<br>Integration</h3>
    </div>
    <p>Lorem ipsum dolor sit amet, Lonsectetur adipiscing elit. Sed pulvinar tempor pellentesque</p>
  </div>

  <div class="service abs" style="left:510px">
    <div class="service-head">
      <svg width="24" height="22" viewBox="0 0 24 22"><circle cx="9" cy="9" r="7" fill="none" stroke="#222" stroke-width="1.6"/><path d="M2 9h14M9 2v14" stroke="#222"/><path d="M10 11h3l2 6h7l1-4h-9" fill="none" stroke="#222" stroke-width="1.6"/><circle cx="16" cy="20" r="1.3" fill="#222"/><circle cx="21" cy="20" r="1.3" fill="#222"/></svg>
      <h3>Digital Commerce</h3>
    </div>
    <p>Lorem ipsum dolor sit amet, Lonsectetur adipiscing elit. Sed pulvinar ellentesque. Lorem ipsum dolor sit amet, Lonsectetur adipis</p>
  </div>

  <div class="service abs" style="left:670px">
    <div class="service-head">
      <svg width="24" height="22" viewBox="0 0 24 22"><rect x="3" y="2" width="16" height="19" fill="none" stroke="#222" stroke-width="2"/><rect x="7" y="1" width="8" height="3" fill="#222"/><path d="M6 9h10M6 13h10M6 17h10" stroke="#222" stroke-width="1.5"/></svg>
      <h3>Application Development<br>&amp; Maintenance</h3>
    </div>
    <p>Lorem ipsum dolor sit amet, Lonsectetur adipiscing elit. Sed pulvinar pellentesque. Lorem ipsum dolor sit amet, Lonsectetur</p>
  </div>

  <div class="divider abs"></div>

  <h2 class="section-title events-title abs">Company <span class="accent">Events</span></h2>
  <div class="slider-arrows abs" style="left:789px;top:720px">
    <svg width="10" height="12" viewBox="0 0 10 12"><path d="M7 1L2 6l5 5" fill="none" stroke="#aaa" stroke-width="2"/></svg>
    <svg width="10" height="12" viewBox="0 0 10 12"><path d="M3 1l5 5-5 5" fill="none" stroke="#aaa" stroke-width="2"/></svg>
  </div>
  <div class="events-band abs"></div>

  <div class="event-media vineyard abs" style="left:168px" role="img" aria-label="Video still of a vineyard with wine glass and grapes">
    <div class="play abs"><svg width="8" height="9" viewBox="0 0 8 9"><path d="M1 0l7 4.5L1 9z" fill="#fff"/></svg></div>
  </div>
  <div class="event-text abs" style="left:353px">
    <h4>Party</h4>
    <p>Lorem ipsum dolor sit amet, Lonsectetur adipiscing elit. Sed pulvinar tempor pellentesque, Lorem ipsum dolor sit amet, Lonsectetur adipiscing elit. Sed pulvinar</p>
  </div>

  <div class="event-media meeting abs" style="left:505px" role="img" aria-label="Photo of colleagues smiling together at an office event"></div>
  <div class="event-text abs" style="left:690px">
    <h4>Party</h4>
    <p>Lorem ipsum dolor sit amet, Lonsectetur adipiscing elit. Sed pulvinar tempor pellentesque, Lorem ipsum dolor sit amet, Lonsectetur adipiscing elit. Sed pulvinar</p>
  </div>

  <h2 class="section-title clients-title abs">Clients</h2>
  <div class="slider-arrows abs" style="left:789px;top:876px">
    <svg width="10" height="12" viewBox="0 0 10 12"><path d="M7 1L2 6l5 5" fill="none" stroke="#aaa" stroke-width="2"/></svg>
    <svg width="10" height="12" viewBox="0 0 10 12"><path d="M3 1l5 5-5 5" fill="none" stroke="#aaa" stroke-width="2"/></svg>
  </div>
  <div class="client abs" style="left:190px">Ledger<br>Cellars</div>
  <div class="client abs" style="left:297px">Vinora<br>Wines</div>
  <div class="client abs" style="left:403px">Ashgrove</div>
  <div class="client abs" style="left:509px">Kellerhaus<br>Weine</div>
  <div class="client abs" style="left:616px">Weekend Post<br>Wine Club</div>
  <div class="client abs" style="left:722px">Southern Cross<br>Wine</div>

  <footer class="site-footer abs"></footer>

  <h3 class="footer-title abs" style="left:197px;top:1014px">Latest opportunities</h3>
  <div class="opp abs" style="top:1049px">
    <div class="opp-thumb" style="background:linear-gradient(120deg,#c9c1b5,#6c6a6a)" role="img" aria-label="Photo of people at a desk"></div>
    <div class="footer-text" style="font-size:8px;line-height:9px">08-01-2014<br>Lorem ipsum dolor sit amet,<br>consectetur adipiscing elit. Sed</div>
  </div>
  <div class="opp abs" style="top:1099px">
    <div class="opp-thumb" style="background:linear-gradient(#1f4fa8,#7fa6e0 60%,#4d8a3a)" role="img" aria-label="Photo of a green field under a blue sky"></div>
    <div class="footer-text" style="font-size:8px;line-height:9px">08-01-2014<br>Lorem ipsum dolor sit amet,<br>consectetur adipiscing elit. Sed</div>
  </div>

  <h3 class="footer-title abs" style="left:422px;top:1013px">About Us</h3>
  <p class="footer-text abs" style="left:422px;top:1035px;width:205px">Lorem ipsum dolor sit amet, conse ctetur adipiscing elit. Sed pulvinar tempor pellentesque. Donec at elementum enim. Morbi malesuada, urna ac adipiscing commodo, nisi leo Sed pulvinar tempor.</p>
  <h3 class="footer-title abs" style="left:422px;top:1096px">Careers</h3>
  <p class="footer-text abs" style="left:422px;top:1118px;width:205px">As the businesses we support develop and grow, so do their needs for strong, innovative IT solutions.</p>

  <h3 class="footer-title abs" style="left:685px;top:1014px">Contact:</h3>
  <div class="footer-text abs" style="left:685px;top:1042px;display:flex;gap:6px;align-items:center">
    <svg width="12" height="10" viewBox="0 0 12 10"><path d="M1 4c0-3 10-3 10 0l-2 1-1-2H4L3 5z" fill="#ddd"/><rect x="3" y="5" width="6" height="4" fill="#ddd"/></svg>+91 (44) 55501234
  </div>
  <div class="footer-text abs" style="left:685px;top:1058px;display:flex;gap:6px;align-items:center">
    <svg width="11" height="10" viewBox="0 0 11 10"><rect x="1" y="1" width="9" height="8" fill="none" stroke="#ddd"/><path d="M1 1l4.5 4L10 1" fill="none" stroke="#ddd"/></svg>contactus@bluefernbs-site.com
  </div>
  <p class="footer-text abs" style="left:685px;top:1079px;width:160px">Bluefern Business Services Pvt. Ltd.<br>4th Floor, Meridian Park Tower<br>Unit C12 Lakeview Industrial Estate<br>Guindy, Chennai, 600099<br>Tamil Nadu</p>

  <div class="footer-bottom abs"></div>
  <div class="copyright abs">© 2014, All Rights Reserved</div>
  <div class="social abs" style="left:689px">Feed</div>
  <div class="social abs" style="left:714px">Chat</div>
  <div class="social abs" style="left:739px">Pins</div>
  <div class="social abs" style="left:764px">Post</div>

</div>
</body>
</html>
```